​Silver Harbor Rhythm provides personal, friendly service in a fun and high energy environment. We are based in Vermont.

We would like a card that appeals to a wide range of audiences as we do a wide range of events. Please feel free to check out our website silverharborrhythm.net for inspiration.

Target Market(s)

weddings, corporate, birthday parties, colleges

Industry/Entity Type

Business

Contact Information for Business Card

Silver Harbor Rhythm
Providing Entertainment For All Occasions
555 274 9160
silverharborrhythm@mailnest.net
silverharborrhythm.net

```html
<!DOCTYPE html>
<html lang="en">
<head>
<meta charset="utf-8">
<title>Silver Harbor Rhythm – Business Card</title>
<link rel="stylesheet" href="https://fonts.googleapis.com/css2?family=Exo+2:wght@500;700&display=swap">
<style>
  :root {
    --bg: #e9e6e1;
    --card: #ffffff;
    --green: #1f6b47;
    --maroon: #8a2f2f;
    --ink: #1c1c1c;
    --faint: #ececec;
    --shadow: rgba(0,0,0,0.18);
  }
  * { margin: 0; padding: 0; box-sizing: border-box; }
  html, body { width: 1200px; height: 913px; overflow: hidden; background: var(--bg); }
  body { position: relative; font-family: "Exo 2", sans-serif; }

  .card {
    position: absolute;
    width: 520px;
    height: 297px;
    background: var(--card);
    box-shadow: 0 6px 18px var(--shadow);
  }
  .card--front { left: 70px; top: 130px; }
  .card--back  { left: 610px; top: 470px; }

  /* Front */
  .brand {
    position: absolute;
    display: flex;
    align-items: center;
    gap: 12px;
    color: var(--green);
    font-weight: 700;
    letter-spacing: 0.02em;
  }
  .brand__square { background: var(--maroon); flex: none; }
  .card--front .brand { left: 50%; top: 50%; transform: translate(-50%, -50%); font-size: 34px; white-space: nowrap; }
  .card--front .brand__square { width: 30px; height: 30px; }

  /* Back */
  .card--back .brand { right: 24px; top: 24px; font-size: 17px; gap: 8px; }
  .card--back .brand__square { width: 14px; height: 14px; }
  .back__decor {
    position: absolute;
    right: 18px; top: 70px;
    width: 170px; height: 150px;
    background: var(--faint);
  }
  .tagline {
    position: absolute;
    left: 28px; top: 64px;
    color: var(--green);
    font-weight: 700;
    font-size: 19px;
    line-height: 1.3;
    letter-spacing: 0.02em;
  }
  .contact {
    position: absolute;
    left: 28px; bottom: 26px;
    list-style: none;
    color: var(--ink);
    font-weight: 500;
    font-size: 16px;
    line-height: 1.45;
  }
  .contact__item { display: flex; align-items: center; gap: 9px; }
  .contact__icon { width: 15px; height: 15px; flex: none; fill: var(--ink); }
</style>
</head>
<body>

  <section class="card card--front" aria-label="Card front">
    <div class="brand"><span class="brand__square"></span>Silver Harbor Rhythm</div>
  </section>

  <section class="card card--back" aria-label="Card back">
    <div class="back__decor"></div>
    <div class="brand"><span class="brand__square"></span>Silver Harbor Rhythm</div>

    <p class="tagline">Silver Harbor Rhythm<br>Providing Entertainment<br>For All Occasions</p>

    <ul class="contact">
      <li class="contact__item">
        <svg class="contact__icon" viewBox="0 0 16 16" aria-hidden="true"><path d="M2 5c0-2 2-3 6-3s6 1 6 3v1h-3V5H5v1H2zM4 7h8l2 7H2z"/></svg>
        555 274 9160
      </li>
      <li class="contact__item">
        <svg class="contact__icon" viewBox="0 0 16 16" aria-hidden="true"><path d="M1 3h14v10H1z M2 4l6 5 6-5" fill="none" stroke="currentColor" stroke-width="1.6"/><path d="M1 3h14v10H1z"/><path d="M2 4l6 5 6-5" fill="none" stroke="#fff" stroke-width="1.3"/></svg>
        silverharborrhythm@mailnest.net
      </li>
      <li class="contact__item">
        <svg class="contact__icon" viewBox="0 0 16 16" aria-hidden="true"><circle cx="8" cy="8" r="7"/><path d="M1 8h14M8 1v14M3 4h10M3 12h10" stroke="#fff" stroke-width="1" fill="none"/></svg>
        www.silverharborrhythm.net
      </li>
    </ul>
  </section>

</body>
</html>
```